Letterhead Design for Law Firm

**Edit: I have added the photo of a bottom that I like.

------
We are looking for a re-design of our new letterhead. The letterhead is for a law firm and will be used for digital and traditionally printed correspondence.

Here are some suggestions:

- Please use colours are #8ec900 and simple black.
- Please do not use any type of "waves" at the bottom of the page. This is not in style at all.
- Please stay modern yet conservative.
- Please use font Segoe UI Light or similar if you can
- Avoid clipart or illustrations.
- Utilize ample white space in the layout so the design looks clean and information is easy to read at a glance. Don't overcrowd the letterhead.
- Make sure the letterhead design is consistent with our brand identity (see corvelith.ca)
-Please, no black headers or footers.

I am attaching my current letterhead and signature for your convenience.

Remember, the letterhead is an extension of our professional identity. We are a successful firm and trial lawyers who correspond with insurers, judges, lawyers, courts, clients, etc. Make it new, modern, attractive, yet powerful and conservative.

It needs to be easily printable. I would like the bleed removed in print so the black bar the bottom crosses the page (but the text is not near the edges)
Updates

Low design quality

Target Market(s)

Clients, Government Offices, Judiciary, Lawyers, Insurance Companies, Colleagues.

Industry/Entity Type

Law

Other font styles liked:
• Segoe UI LIght, Calibri Light,

Colors
00AB8E
00BBA5
67D7C9
C6EFE9
E9F9F6

Requirements
Must have
• Everything that is on the letterhead now.
Nice to have
• Cutting Edge design, yet conservative.
Should not have
• law firm cliche design, images,

```html
<!DOCTYPE html>
<html lang="en">
<head>
<meta charset="utf-8">
<title>Corvelith Personal Injury Lawyers – Letterhead</title>
<link rel="stylesheet" href="https://fonts.googleapis.com/css2?family=Open+Sans:wght@300;400;600&display=swap">
<style>
  :root {
    --brand-green: #8ec900;
    --ink: #1f1f1f;
    --ink-soft: #333333;
    --paper: #ffffff;
    --backdrop: #ececec;
  }
  html, body {
    margin: 0;
    padding: 0;
    width: 1200px;
    height: 1141px;
    overflow: hidden;
    background: var(--backdrop);
    font-family: "Open Sans", "Segoe UI", sans-serif;
    color: var(--ink);
  }
  .letterhead {
    position: absolute;
    left: 211px;
    top: 20px;
    width: 778px;
    height: 1100px;
    background: var(--paper);
    box-shadow: 0 2px 8px rgba(0,0,0,0.12);
  }
  .edge-bar {
    position: absolute;
    left: 0; top: 0;
    width: 11px; height: 100%;
    background: var(--brand-green);
  }
  .line {
    position: absolute;
    left: 53px;
    margin: 0;
    font-size: 13.5px;
    font-weight: 300;
    line-height: 18.4px;
    white-space: nowrap;
  }
  .line.strong { font-weight: 400; }
  .recipient { top: 158px; }
  .re-label { left: 53px; top: 442px; font-weight: 400; }
  .re-block { left: 220px; top: 442px; font-weight: 400; }
  .rule {
    position: absolute;
    left: 53px;
    width: 673px;
    height: 2px;
    background: var(--brand-green);
  }
  .signature-mark {
    position: absolute;
    left: 53px;
    top: 765px;
    width: 210px;
    height: 50px;
    background: linear-gradient(90deg, #f2f2f2, #e4e4e4);
  }
  .footer-name {
    position: absolute;
    left: 53px;
    top: 978px;
    margin: 0;
    font-size: 50px;
    font-weight: 400;
    line-height: 60px;
    letter-spacing: 1px;
    color: var(--ink);
  }
  .footer-tagline {
    position: absolute;
    left: 56px;
    top: 1046px;
    margin: 0;
    font-size: 13.5px;
    font-weight: 400;
    letter-spacing: 1.6px;
    color: var(--ink);
  }
  .practice-areas {
    position: absolute;
    right: 227px;
    top: 981px;
    margin: 0;
    padding: 0;
    list-style: none;
    text-align: right;
    font-size: 10.5px;
    font-weight: 300;
    line-height: 13px;
    color: var(--ink-soft);
  }
  .practice-areas .heading { color: var(--brand-green); font-weight: 600; }
  .footer-divider {
    position: absolute;
    left: 568px;
    top: 972px;
    width: 1px;
    height: 100px;
    background: var(--brand-green);
  }
  .contact {
    position: absolute;
    left: 584px;
    margin: 0;
    font-size: 9.8px;
    font-weight: 400;
    line-height: 13px;
    color: var(--ink-soft);
    white-space: nowrap;
  }
  .contact svg {
    width: 7px; height: 8px;
    margin-right: 4px;
    vertical-align: -1px;
    fill: var(--brand-green);
  }
  .contact .indent { padding-left: 11px; }
  .file-clerk-label { color: var(--brand-green); font-weight: 600; }
</style>
</head>
<body>
  <main class="letterhead">
    <div class="edge-bar"></div>

    <p class="line strong" style="top:30px">Without Prejudice</p>
    <p class="line" style="top:67px">March 13, 2024</p>
    <p class="line strong" style="top:103px">By Email</p>

    <address class="line recipient" style="font-style:normal">
      Northvale Insurance Company<br>
      Claims Litigation Department<br>
      48 Harrow Lane South<br>
      P.O. Box 1200<br>
      Kitchener, ON&nbsp;&nbsp;&nbsp;N2A 1B3
    </address>

    <p class="line" style="top:268px">Attention:&nbsp; Mr. Dorian Fell</p>
    <p class="line" style="top:305px">Mr. Fell:</p>

    <p class="line re-label">Re:</p>
    <p class="line re-block">
      Marsh v. Delacroix et al.<br>
      DOL:&nbsp; September 12, 2019<br>
      Pre-Mediation Settlement Proposal – March 13th, 2024
    </p>

    <div class="rule" style="top:408px"></div>
    <div class="rule" style="top:702px"></div>

    <p class="line" style="top:713px">Yours very truly,<br>CORVELITH PERSONAL INJURY LAWYERS</p>

    <div class="signature-mark" role="img" aria-label="Handwritten signature of Owen T. Corvelith"></div>

    <p class="line" style="top:837px; line-height:21px">
      Owen T. Corvelith<br>
      Corvelith Law Professional Corporation<br>
      /nw<br>
      Encl.
    </p>

    <footer>
      <p class="footer-name">CORVELITH</p>
      <p class="footer-tagline">PERSONAL INJURY LAWYERS</p>

      <ul class="practice-areas">
        <li class="heading">Practice Restricted</li>
        <li>Serious Personal Injury</li>
        <li>Wrongful Death Litigation</li>
        <li>Long-Term Disability Litigation</li>
        <li>Wrongful Dismissal Litigation</li>
        <li>Employee Terminations</li>
      </ul>

      <div class="footer-divider"></div>

      <p class="contact" style="top:971px">
        <svg viewBox="0 0 10 12"><path d="M5 0a4 4 0 0 0-4 4c0 3 4 8 4 8s4-5 4-8a4 4 0 0 0-4-4zm0 5.6A1.6 1.6 0 1 1 5 2.4a1.6 1.6 0 0 1 0 3.2z"/></svg>12 Elm Street W., Suite 904<br>
        <span class="indent">Hamilton, ON&nbsp; L8P 2B7</span>
      </p>
      <p class="contact" style="top:1001px">
        <svg viewBox="0 0 12 10"><path d="M1 3c0-2 10-2 10 0v1.5H8.5V3h-5v1.5H1zM3 5h6l2 4H1z"/></svg>905-555-0142<br>
        <svg viewBox="0 0 10 10"><path d="M2 0h6v3H2zM0 4h10v6H0zm2 2v1h2V6zm4 0v1h2V6z"/></svg>905-555-0187<br>
        <svg viewBox="0 0 12 9"><path d="M0 0h12L6 5zM0 2l6 4 6-4v7H0z"/></svg>nora@corvelith.ca<br>
        <svg viewBox="0 0 10 10"><circle cx="5" cy="5" r="5"/></svg>www.CORVELITH.ca
      </p>
      <p class="contact" style="top:1061px">
        <span class="file-clerk-label">File Clerk:</span> Nora Whitlock
      </p>
    </footer>
  </main>
</body>
</html>
```